Property Developer - Simple yet Sophisticated and Sharp Business Card

We are a medium sized property developer involved mainly in townhouse developments and land subdivisions.

The company is looking for a simple, sharp and sophisticated business card that will be given to contractors, land owners, financiers etc and thus will need to look professional.

Property development related graphics and art can be used, however the card is not to be too "busy" or crowded. Our company name is Kestrel Developments which could possibly be incorporated into the graphics or artwork.

Single sided and/or double sided designs will be acceptable.

A Simple, Sophisticated, Sharp design please!

Good Luck !

```html
<!DOCTYPE html>
<html lang="en">
<head>
<meta charset="utf-8">
<title>Kestrel Developments – Business Card</title>
<link rel="stylesheet" href="https://fonts.googleapis.com/css2?family=Barlow:wght@300;400;700&display=swap">
<style>
  :root {
    --brown: #4a3517;
    --muted: #8a8278;
    --paper: #ffffff;
  }
  * { margin: 0; padding: 0; box-sizing: border-box; }
  html, body {
    width: 1200px;
    height: 900px;
    overflow: hidden;
    background: var(--paper);
  }
  .canvas {
    position: relative;
    width: 1200px;
    height: 900px;
    font-family: "Barlow", "Helvetica Neue", Arial, sans-serif;
    color: var(--brown);
  }
  .card {
    position: absolute;
    left: 66px;
    top: 126px;
    width: 1064px;
    height: 650px;
    background: var(--paper);
  }
  .band {
    position: absolute;
    left: 0;
    width: 100%;
    height: 50px;
    background: var(--brown);
  }
  .band--top { top: 0; }
  .band--bottom { bottom: 0; }
  .rule {
    position: absolute;
    left: 0;
    width: 100%;
    background: var(--brown);
  }
  .rule--top-thick { top: 55px; height: 3px; }
  .rule--top-thin { top: 64px; height: 2px; }
  .rule--divider { top: 463px; height: 2px; }
  .rule--bottom-thin { top: 588px; height: 2px; }
  .rule--bottom-thick { top: 595px; height: 3px; }

  .company-name {
    position: absolute;
    left: 94px;
    top: 86px;
    font-size: 40px;
    font-weight: 700;
    letter-spacing: 0.5px;
    line-height: 1;
  }
  .person { position: absolute; left: 94px; top: 406px; }
  .person__name {
    font-size: 24px;
    font-weight: 700;
    line-height: 1;
  }
  .person__role {
    margin-top: 4px;
    font-size: 14px;
    font-weight: 400;
    color: var(--muted);
    letter-spacing: 0.3px;
    line-height: 1;
  }
  .contact {
    position: absolute;
    top: 478px;
  }
  .contact--phone { left: 94px; }
  .contact--email { left: 314px; }
  .contact--postal { left: 734px; }
  .contact__label {
    font-size: 14px;
    font-weight: 400;
    color: var(--muted);
    letter-spacing: 0.3px;
    line-height: 16px;
  }
  .contact__value {
    font-size: 24px;
    font-weight: 400;
    line-height: 29px;
    letter-spacing: 0.4px;
  }
  .contact__value + .contact__label { margin-top: 5px; }
</style>
</head>
<body>
<div class="canvas">
  <div class="card">
    <div class="band band--top"></div>
    <div class="rule rule--top-thick"></div>
    <div class="rule rule--top-thin"></div>

    <h1 class="company-name">KESTREL DEVELOPMENTS</h1>

    <div class="person">
      <p class="person__name">DANIEL HART</p>
      <p class="person__role">PROJECT MANAGER</p>
    </div>

    <div class="rule rule--divider"></div>

    <div class="contact contact--phone">
      <p class="contact__label">PHONE</p>
      <p class="contact__value">(07) 3000 1274</p>
      <p class="contact__label">FAX</p>
      <p class="contact__value">(07) 3000 6832</p>
    </div>

    <div class="contact contact--email">
      <p class="contact__label">EMAIL</p>
      <p class="contact__value">PROJECTS.KESTRELHOMES<br>@EXAMPLE.COM</p>
    </div>

    <div class="contact contact--postal">
      <p class="contact__label">POSTAL</p>
      <p class="contact__value">PO BOX 2471<br>MAPLEWOOD SOUTH<br>QLD 4999</p>
    </div>

    <div class="rule rule--bottom-thin"></div>
    <div class="rule rule--bottom-thick"></div>
    <div class="band band--bottom"></div>
  </div>
</div>
</body>
</html>
```